Tolvane Inc., a third party debt collection agency needs a Website

Tolvane needs a very basic website (3 basic pages) so that consumers can download forms, potential employees can get required EEO language and see potential jobs, and to show that they are a consumer friendly organization.

I've attached a list of requirements and wishes titled "Tolvane Website Specifications"

Target Market(s)

Consumers that need to repay their government loans; Tolvane will walk through the process to assist them.

Industry/Entity Type

Financial Service

Coding

Coded - Design and coding required

Number of Pages Required

1 page

Font styles to use
Sans Serif

Colors
0355a3

Requirements
Must have
• Tolvane Logo
• See document "Tolvane Website Specifications" for all requirements

```html
<!DOCTYPE html>
<html lang="en">
<head>
<meta charset="utf-8">
<title>Tolvane Inc.</title>
<link rel="stylesheet" href="https://fonts.googleapis.com/css2?family=Open+Sans:wght@400;600;700&display=swap">
<style>
:root{
  --navy:#27276f;
  --navy-deep:#1e1e5c;
  --red:#8f1a1f;
  --red-band:#8e1b20;
  --grey-bar:#555a5f;
  --text:#444;
  --muted:#666;
  --white:#fff;
}
*{box-sizing:border-box;margin:0;padding:0}
html,body{width:667px;height:1200px;overflow:hidden;background:var(--white)}
body{font-family:"Open Sans",Arial,sans-serif;color:var(--text);position:relative}
.abs{position:absolute}

/* header */
.site-header{position:absolute;left:0;top:0;width:667px;height:77px;border-top:2px solid var(--navy);background:var(--white)}
.brand{position:absolute;left:89px;top:30px;display:flex;align-items:center;gap:6px}
.brand-mark{width:12px;height:12px;border-radius:50%;background:var(--navy)}
.brand-name{font-weight:700;font-size:17px;color:var(--red);letter-spacing:-.2px}
.contact-row{position:absolute;right:90px;top:14px;display:flex;gap:18px;font-size:7px;color:var(--muted)}
.contact-item{display:flex;align-items:center;gap:6px}
.contact-icon{width:14px;height:14px;border:1px solid var(--red);border-radius:50%;display:flex;align-items:center;justify-content:center}
.main-nav{position:absolute;left:252px;top:46px;display:flex;gap:23px;font-size:7px;font-weight:600;color:#333}
.main-nav .active{color:var(--navy);position:relative}
.main-nav .active::after{content:"";position:absolute;left:0;right:0;top:11px;height:2px;border-radius:2px;background:var(--navy)}
.search-btn{position:absolute;left:556px;top:41px;width:20px;height:20px;border-radius:50%;background:var(--navy);display:flex;align-items:center;justify-content:center}

/* hero */
.hero{position:absolute;left:0;top:77px;width:667px;height:279px;background:linear-gradient(100deg,#3a3433 0%,#8c8480 22%,#d9d9dc 45%,#eef0f2 65%,#c5c8cc 100%)}
.hero-arrow{position:absolute;top:112px}
.hero-caption{position:absolute;left:312px;top:104px}
.quote-tab{position:absolute;left:0;top:0;width:120px;height:26px;background:var(--red);color:var(--white);font-size:8px;font-weight:700;display:flex;align-items:center;justify-content:center;clip-path:polygon(0 0,100% 0,100% 100%,8% 100%)}
.welcome-bar{position:absolute;left:120px;top:0;width:235px;height:26px;background:var(--grey-bar);color:var(--white);font-size:10px;font-weight:700;display:flex;align-items:center;padding-left:12px}
.hero-sub{position:absolute;left:6px;top:30px;width:349px;height:30px;background:rgba(85,90,95,.82);color:#eee;font-size:6px;line-height:9px;padding:6px 12px}
.hero-menu{position:absolute;left:597px;top:195px}
.hero-wave{position:absolute;left:0;bottom:-1px}

/* welcome */
.intro{position:absolute;left:90px;top:380px;width:268px}
.section-title{font-size:15px;font-weight:700;color:var(--navy-deep)}
.section-title .accent{color:var(--red)}
.intro p{font-size:5.6px;line-height:10.8px;margin-top:6px;color:#555}
.btn{display:flex;width:62px;height:17px;font-size:5.4px;font-weight:600;color:var(--white);text-transform:uppercase}
.btn-label{flex:1;background:var(--red);display:flex;align-items:center;padding-left:7px}
.btn-arrow{width:16px;background:var(--navy);display:flex;align-items:center;justify-content:center}
.video{position:absolute;left:368px;top:385px;width:209px;height:127px;background:linear-gradient(120deg,#e5e4e0 0%,#9a9c9f 45%,#3b3f48 100%)}
.video-play{position:absolute;left:93px;top:52px}

/* why band */
.why{position:absolute;left:0;top:544px;width:667px;height:222px;background:var(--red-band)}
.why-notch{position:absolute;left:320px;top:0}
.why h2{position:absolute;left:0;width:100%;top:32px;text-align:center;color:var(--white);font-size:14px;font-weight:700}
.feature{position:absolute;top:71px;width:100px;text-align:center;color:var(--white)}
.feature-ring{width:52px;height:52px;margin:0 auto;border-radius:50%;border:2px solid var(--white);display:flex;align-items:center;justify-content:center}
.feature-core{width:44px;height:44px;border-radius:50%;background:var(--white);display:flex;align-items:center;justify-content:center}
.feature h3{font-size:7.4px;font-weight:700;margin-top:11px}
.feature p{font-size:5.6px;line-height:10.4px;margin-top:4px}

/* cards */
.photo{position:absolute;border:2px solid #e3e3e3}
.card-title{position:absolute;font-size:11px;font-weight:700;color:var(--navy-deep)}
.card-text{position:absolute;font-size:5.6px;line-height:10.8px;color:#555}
.news-meta{position:absolute;left:90px;top:935px;font-size:5.6px;color:var(--red)}

/* footer */
.site-footer{position:absolute;left:0;top:1052px;width:667px;height:112px;background:var(--navy)}
.partner-badge{position:absolute;left:90px;top:24px;width:68px;height:68px;border-radius:50%;background:var(--white)}
.foot-col{position:absolute;top:24px;color:var(--white)}
.foot-col h4{font-size:6.6px;font-weight:600;letter-spacing:.2px}
.foot-col ul{list-style:none;margin-top:7px}
.foot-col li{font-size:5.6px;line-height:11px}
.foot-divider{position:absolute;top:22px;width:1px;height:72px;background:rgba(255,255,255,.25)}
.trust-badge{position:absolute;left:514px;top:28px;width:50px;height:40px;border-radius:4px;background:rgba(255,255,255,.9)}
.footer-bar{position:absolute;left:0;top:1164px;width:667px;height:36px;background:var(--navy-deep)}
.copyright{position:absolute;left:90px;top:14px;font-size:5.6px;color:var(--white)}
.social{position:absolute;top:7px;width:21px;height:21px;border-radius:50%;background:#3a3a85}
</style>
</head>
<body>

<header class="site-header">
  <div class="brand"><span class="brand-mark"></span><span class="brand-name">Tolvane, Inc.</span></div>
  <div class="contact-row">
    <div class="contact-item">
      <span class="contact-icon"><svg width="7" height="5" viewBox="0 0 7 5"><rect width="7" height="5" fill="#8f1a1f"/><path d="M0 0L3.5 3L7 0" stroke="#fff" stroke-width=".7" fill="none"/></svg></span>
      Email: info@company.Com
    </div>
    <div class="contact-item">
      <span class="contact-icon"><svg width="7" height="7" viewBox="0 0 10 10"><path d="M2 1l2 2-1 1.5c.7 1.3 1.5 2.1 2.5 2.5L7 6l2 2-1.5 1.5C4.5 9 1 5.5.5 2.5z" fill="#8f1a1f"/></svg></span>
      Phone: 000-000-0009
    </div>
  </div>
  <nav class="main-nav">
    <span class="active">HOME</span><span>OUR SERVICES</span><span>ABOUT US</span><span>CLIENT LIST</span><span>CONTACT US</span>
  </nav>
  <div class="search-btn"><svg width="7" height="7" viewBox="0 0 10 10"><circle cx="4" cy="4" r="3" stroke="#fff" stroke-width="1.5" fill="none"/><path d="M6.3 6.3L9 9" stroke="#fff" stroke-width="1.5"/></svg></div>
</header>

<section class="hero" role="img" aria-label="Photo of smiling call centre agents wearing headsets at their desks">
  <svg class="hero-arrow" style="left:24px" width="14" height="30" viewBox="0 0 14 30"><path d="M13 1L1 15l12 14" stroke="#fff" stroke-width="1.2" fill="none"/></svg>
  <svg class="hero-arrow" style="left:628px" width="14" height="30" viewBox="0 0 14 30"><path d="M1 1l12 14L1 29" stroke="#fff" stroke-width="1.2" fill="none"/></svg>
  <div class="hero-caption">
    <div class="quote-tab">GET A QUOTE &#10140;</div>
    <div class="welcome-bar">WELCOME TO TOLVANE</div>
    <div class="hero-sub">Lorem ipsum dolor sit amet, consectetur adipiscing elit, sed do eiusmod temporne ididunt ut labore et dolore magna aliqua. Ut enim ad minim veniam.</div>
  </div>
  <svg class="hero-menu" width="14" height="16" viewBox="0 0 14 16"><rect x="0" y="0" width="14" height="1.5" fill="#c0272d"/><rect x="4" y="5" width="8" height="1.5" fill="#fff"/><rect x="4" y="9" width="8" height="1.5" fill="#fff"/><rect x="4" y="13" width="8" height="1.5" fill="#fff"/></svg>
  <svg class="hero-wave" width="667" height="50" viewBox="0 0 667 50" preserveAspectRatio="none">
    <path d="M0 18 Q230 68 667 14 L667 50 L0 50Z" fill="#fff"/>
    <path d="M0 18 Q230 68 667 14" stroke="#27276f" stroke-width="3" fill="none"/>
  </svg>
</section>

<section class="intro">
  <h1 class="section-title">Welcome to <span class="accent">Tolvane</span></h1>
  <p>Tolvane is a third party debt collection agency that is focused on the collection of higher education loans. Tolvane is compliant with all federal, state, and local laws and is committed to the professional and fair treatment of consumers. Our goal is to assist consumers in resolving their obligations in the manner that best meets their needs and to provide information necessary in order for consumers to make an informed decision.</p>
  <p>Sed ut perspiciatis unde omnis iste natus error sit voluptatem accusantium doloremque lauda ntim, totam rem aperiam, eaque ipsa quae ab illo inventore veritatis et quasi archit</p>
  <div class="btn" style="margin-top:10px"><span class="btn-label">Read More</span><span class="btn-arrow">&#10140;</span></div>
</section>
<div class="video" role="img" aria-label="Video still of two businessmen reviewing a tablet at a desk">
  <svg class="video-play" width="24" height="24" viewBox="0 0 24 24"><circle cx="12" cy="12" r="11" fill="#fff"/><circle cx="12" cy="12" r="9" fill="#d0202a"/><path d="M10 8l6 4-6 4z" fill="#fff"/></svg>
</div>

<section class="why">
  <svg class="why-notch" width="27" height="13" viewBox="0 0 27 13"><path d="M0 0h27L13.5 13z" fill="#fff"/></svg>
  <h2>Why Tolvane?</h2>
  <div class="feature" style="left:83px">
    <div class="feature-ring"><div class="feature-core"><svg width="14" height="12" viewBox="0 0 14 12"><path d="M1 0v11h13" stroke="#8e1b20" stroke-width="1.2" fill="none"/><rect x="3" y="6" width="2" height="4" fill="#8e1b20"/><rect x="6" y="3" width="2" height="7" fill="#8e1b20"/><rect x="9" y="5" width="2" height="5" fill="#8e1b20"/></svg></div></div>
    <h3>BONORUM</h3><p>Lorem ipsum dolor sit amet, consectetur adipiscing elit, sed do eiusmod tempor.</p>
  </div>
  <div class="feature" style="left:184px">
    <div class="feature-ring"><div class="feature-core"><svg width="14" height="13" viewBox="0 0 14 13"><path d="M7 0L0 3.5h14z" fill="#8e1b20"/><rect x="1.5" y="4.5" width="2" height="5" fill="#8e1b20"/><rect x="6" y="4.5" width="2" height="5" fill="#8e1b20"/><rect x="10.5" y="4.5" width="2" height="5" fill="#8e1b20"/><rect x="0" y="10.5" width="14" height="2" fill="#8e1b20"/></svg></div></div>
    <h3>ALORUM</h3><p>Lorem ipsum dolor sit amet, consectetur adipiscing elit, sed do eiusmod tempor.</p>
  </div>
  <div class="feature" style="left:284px">
    <div class="feature-ring"><div class="feature-core"><svg width="13" height="13" viewBox="0 0 13 13"><path d="M11 5A4.7 4.7 0 0 0 2.5 3.5M2 8a4.7 4.7 0 0 0 8.5 1.5" stroke="#8e1b20" stroke-width="1.8" fill="none"/><path d="M1 1v4h4z" fill="#8e1b20"/><path d="M12 12V8H8z" fill="#8e1b20"/></svg></div></div>
    <h3>SNORUMLO</h3><p>Lorem ipsum dolor sit amet, consectetur adipiscing elit, sed do eiusmod tempor.</p>
  </div>
  <div class="feature" style="left:385px">
    <div class="feature-ring"><div class="feature-core"><svg width="13" height="13" viewBox="0 0 13 13"><path d="M1 0h6v3H4v7H1z" fill="#8e1b20"/><path d="M5 4h5l3 3v6H5z" fill="#8e1b20"/><path d="M10 4v3h3" fill="#fff"/></svg></div></div>
    <h3>ETALORUM</h3><p>Lorem ipsum dolor sit amet, consectetur adipiscing elit, sed do eiusmod tempor.</p>
  </div>
  <div class="feature" style="left:486px">
    <div class="feature-ring"><div class="feature-core"><svg width="13" height="13" viewBox="0 0 13 13"><path d="M13 0L0 5l5 2 2 6z" fill="#8e1b20"/></svg></div></div>
    <h3>BALORUM</h3><p>Lorem ipsum dolor sit amet, consectetur adipiscing elit, sed do eiusmod tempor.</p>
  </div>
</section>

<div class="photo" style="left:90px;top:794px;width:178px;height:111px;background:linear-gradient(90deg,#a8c4de 0%,#d8c8bb 55%,#f1ece8 100%)" role="img" aria-label="Photo of a smiling support agent with a headset in front of her team"></div>
<h2 class="card-title" style="left:90px;top:912px">Latest News</h2>
<div class="news-meta">&#128197; Apr 05 2016 &#128172; Comments</div>
<p class="card-text" style="left:90px;top:954px;width:176px">Sed ut perspiciatis unde omnis iste natus error sit voluptatem accusantium doloremque laudantium, totam rem aperiam, ea que ipsa quae ab illo inventore veritatis et quasi architectobea tae vitae dicta sunt explicmo enim ipsam volupta</p>
<div class="btn abs" style="left:90px;top:1006px"><span class="btn-label">Read More</span><span class="btn-arrow">&#10140;</span></div>

<div class="photo" style="left:288px;top:794px;width:110px;height:109px;background:linear-gradient(135deg,#d9dde3 0%,#8f98a4 55%,#4f5662 100%)" role="img" aria-label="Photo of colleagues meeting around an office desk"></div>
<h2 class="card-title" style="left:407px;top:794px">Consumer <span style="color:var(--red)">Information</span></h2>
<p class="card-text" style="left:407px;top:816px;width:176px">Sed ut perspiciatis unde omnis iste natus error sit voluptatem accusantium doloremque laudantium, totam rem aperiam, ea que ipsa quae ab illo inventore veritatis et quasi architectobea tae vitae dicta sunt explicabo. Nemo enim ipsam voluptatem uia voluptas sit aspernatur aut odit aut fugi.</p>
<div class="btn abs" style="left:407px;top:882px"><span class="btn-label">Read More</span><span class="btn-arrow">&#10140;</span></div>

<div class="photo" style="left:288px;top:918px;width:110px;height:109px;background:linear-gradient(120deg,#c7ced8 0%,#9aa6b6 50%,#e4ddd6 100%)" role="img" aria-label="Photo of a smiling businesswoman with a colleague"></div>
<h2 class="card-title" style="left:407px;top:918px">Careers @ Tolvane</h2>
<p class="card-text" style="left:407px;top:940px;width:176px">Sed ut perspiciatis unde omnis iste natus error sit voluptatem accusantium doloremque laudantium, totam rem aperiam, ea que ipsa quae ab illo inventore veritatis et quasi architectobea tae vitae dicta sunt explicabo. Nemo enim ipsam voluptatem uia voluptas sit aspernatur aut odit aut fugi.</p>
<div class="btn abs" style="left:407px;top:1006px"><span class="btn-label">Read More</span><span class="btn-arrow">&#10140;</span></div>

<footer class="site-footer">
  <div class="partner-badge" role="img" aria-label="Partner association badge"></div>
  <div class="foot-col" style="left:188px"><h4>NAVIGATION</h4><ul><li>Home</li><li>Features</li><li>Pricing</li><li>News</li><li>Contact</li><li>Log In</li></ul></div>
  <div class="foot-divider" style="left:252px"></div>
  <div class="foot-col" style="left:280px"><h4>OUR SERVICES</h4><ul><li>Credit Card Help</li><li>Third party debt collection</li><li>Free Consultation</li><li>About Us</li><li>Privacy Policy</li></ul></div>
  <div class="foot-divider" style="left:373px"></div>
  <div class="foot-col" style="left:398px"><h4>OTHER LINKS</h4><ul><li>No server hardware</li><li>No software to install</li><li>No in-house IT skills</li><li>Full Audit Trails</li><li>Free Client Access</li></ul></div>
  <div class="foot-divider" style="left:478px"></div>
  <div class="trust-badge" role="img" aria-label="Accreditation badge"></div>
</footer>
<div class="footer-bar">
  <p class="copyright">© 2016 tolvane. All copyrights are reserved &nbsp;Term of Use, Privacy Policy</p>
  <span class="social" style="left:485px"></span>
  <span class="social" style="left:508px"></span>
  <span class="social" style="left:531px"></span>
  <span class="social" style="left:554px"></span>
</div>

</body>
</html>
```